Yard Sign Design for Roofing Contractor

We are looking for a new design for our yard signs used on all jobs we build. We are looking for a way to brand the company and are hoping that this contest can give us a "theme" we can incorporate into out other marketing items such as, vehicle graphics, apparel, etc... I have attached a copy of our logo to be used on the sign, it can be "shadowed" with a color to enhance the look and the sign, but please keep the basic logo design. Attached are some samples of construction colors the boss was thinking of along with a picture of our current yard sign to help give some direction and let you know what info is needed on the sign.The darker construction yellow may work better than the fluorescent yellow, but won't know without visual aid. We are not tied to any particular color as of now, so they do have freedom of design as long as keeping with the construction feel. (Just another thought, potentially a reflective construction tape look would be interesting so signs are visable at night)
Updates

Reason: Meeting with new web designers next week to discuss best option to incorporate into our website.Thank you for the submissions!

Target Market(s)

Want signs to stand out when driving by and visibility in neighborhood where sign is posted for potential referrals

Industry/Entity Type

Contractor

Colors
fbed22
fece3e
f37122

Requirements
Must have
• Information that is on our current signs, image attached. I uploaded a .pdf file showing some options that could work for adding "shading" to our logo if you choose to do so.
• Sign should measure 18" T, 24" W
Nice to have
• Interested is seeing designs using construction tape look, images attached

```html
<!DOCTYPE html>
<html lang="en">
<head>
<meta charset="utf-8">
<title>Hartwell Construction – Yard Sign</title>
<link rel="stylesheet" href="https://fonts.googleapis.com/css2?family=Archivo+Black&family=Noto+Serif:wght@700&display=swap">
<style>
  :root {
    --sign-orange: #e8761a;
    --sign-orange-deep: #e06c17;
    --sign-yellow: #f5b21c;
    --sign-yellow-light: #fbc42a;
    --ray-yellow: rgba(251, 196, 40, 0.55);
    --hat-yellow: #fbd22a;
    --hat-shade: #e3ab17;
    --panel-white: #ffffff;
    --ink: #1a1a1a;
  }
  html, body {
    margin: 0;
    padding: 0;
    width: 1200px;
    height: 897px;
    overflow: hidden;
    background: #ffffff;
  }
  .yard-sign {
    position: relative;
    width: 1200px;
    height: 897px;
    overflow: hidden;
  }
  .sunburst-backdrop {
    position: absolute;
    inset: 0;
    background:
      radial-gradient(ellipse 60% 55% at 50% 42%, var(--ray-yellow) 0%, rgba(251,196,40,0) 75%),
      linear-gradient(180deg, var(--sign-orange) 0%, var(--sign-orange-deep) 45%, var(--sign-yellow) 72%, var(--sign-yellow-light) 100%);
  }
  .sign-art {
    position: absolute;
    inset: 0;
  }
  .hard-hat {
    position: absolute;
    left: 548px;
    top: 18px;
    width: 266px;
    height: 204px;
    background: radial-gradient(ellipse 50% 50% at 50% 50%, var(--hat-yellow) 0%, var(--hat-yellow) 40%, var(--hat-shade) 70%, rgba(227,171,23,0) 100%);
  }
  .company-name {
    font-family: "Noto Serif", Georgia, serif;
    font-weight: 700;
    fill: var(--ink);
  }
  .services {
    position: absolute;
    left: 374px;
    top: 563px;
    width: 496px;
    display: flex;
    justify-content: space-between;
    margin: 0;
    padding: 0;
    list-style: none;
    font-family: "Noto Serif", Georgia, serif;
    font-weight: 700;
    font-size: 27px;
    line-height: 1;
    color: var(--ink);
  }
  .phone {
    position: absolute;
    left: 0;
    top: 752px;
    width: 1200px;
    margin: 0;
    text-align: center;
    font-family: "Archivo Black", "Arial Black", sans-serif;
    font-size: 114px;
    line-height: 1;
    letter-spacing: 2px;
    color: var(--ink);
  }
</style>
</head>
<body>
  <main class="yard-sign">
    <div class="sunburst-backdrop" role="img" aria-label="Orange and yellow sunburst rays with paint splatter radiating from the centre"></div>

    <svg class="sign-art" width="1200" height="897" viewBox="0 0 1200 897" aria-labelledby="sign-name">
      <polygon points="72,448 612,160 1152,448 612,755" fill="var(--panel-white)"/>
      <text id="sign-name" class="company-name">
        <tspan x="378" y="483" font-size="100" textLength="488" lengthAdjust="spacingAndGlyphs">HARTWELL</tspan>
        <tspan x="384" y="538" font-size="56" textLength="480" lengthAdjust="spacingAndGlyphs">CONSTRUCTION</tspan>
      </text>
    </svg>

    <div class="hard-hat" role="img" aria-label="Yellow construction hard hat resting on the top corner of the panel"></div>

    <ul class="services">
      <li>ROOF</li>
      <li>SIDING</li>
      <li>GUTTERS</li>
    </ul>

    <p class="phone">555-218-0467</p>
  </main>
</body>
</html>
```